Label & logo reformatting & improving

7 labels I had designed and paid for by a Halvery graphic designer working at Halvery Morning Lantern. Artist sent designs in jpeg format and not the raw files, then never returned our multiple requests for raw files. Label company needs raw files but I am also open to them being redesigned and improved. Or perhaps just background imaging i.e. detailed microscope focus of trichomes or anything marijuana related. Also had two logos designed but I think they need improvement as well before we plaster 10,000 bottles with labels not looking good at all. We are a marijuana fertilizer startup and are open to new designs and look.

```html
<!DOCTYPE html>
<html lang="en">
<head>
<meta charset="utf-8">
<title>Brightvale Hydroponics – Good Roots Label</title>
<link rel="stylesheet" href="https://fonts.googleapis.com/css2?family=Oswald:wght@300;500&family=Staatliches&display=swap">
<style>
  :root {
    --page: #ffffff;
    --label: #3d1819;
    --gold: #d6b769;
    --ink-light: #ffffff;
    --art-green: #7f9a6e;
  }
  html, body {
    margin: 0;
    padding: 0;
    width: 1200px;
    height: 1000px;
    overflow: hidden;
    background: var(--page);
  }
  .canvas {
    position: relative;
    width: 1200px;
    height: 1000px;
  }
  .label {
    position: absolute;
    left: 315px;
    top: 104px;
    width: 570px;
    height: 792px;
    background: var(--label);
  }
  .brand-name {
    position: absolute;
    left: 0;
    width: 100%;
    top: 250px;
    margin: 0;
    text-align: center;
    font-family: "Oswald", sans-serif;
    font-weight: 500;
    color: var(--gold);
    font-size: 46px;
    line-height: 1.1;
    letter-spacing: 3px;
  }
  .brand-name .brand-line { display: block; }
  .brand-rules {
    position: absolute;
    left: 60px;
    top: 370px;
    width: 450px;
    height: 20px;
  }
  .product-name {
    position: absolute;
    left: 108px;
    top: 436px;
    margin: 0;
    font-family: "Staatliches", sans-serif;
    font-weight: 400;
    color: var(--gold);
    font-size: 66px;
    line-height: 0.95;
    letter-spacing: 2px;
  }
  .product-name span { display: block; }
  .emblem {
    position: absolute;
    left: 269px;
    top: 378px;
    width: 228px;
    height: 228px;
  }
  .volume {
    position: absolute;
    left: 0;
    width: 100%;
    top: 650px;
    text-align: center;
    font-family: "Oswald", sans-serif;
    font-weight: 300;
    color: var(--ink-light);
    font-size: 23px;
    line-height: 38px;
  }
  .volume p { margin: 0; }
</style>
</head>
<body>
<div class="canvas">
  <section class="label">
    <h1 class="brand-name">
      <span class="brand-line">BRIGHTVALE</span>
      <span class="brand-line">HYDROPONICS</span>
    </h1>

    <svg class="brand-rules" viewBox="0 0 450 20" aria-hidden="true">
      <line x1="0" y1="4" x2="450" y2="4" stroke="var(--gold)" stroke-width="2"/>
      <line x1="30" y1="14" x2="420" y2="14" stroke="var(--gold)" stroke-width="1.2"/>
    </svg>

    <h2 class="product-name"><span>GOOD</span><span>ROOTS</span></h2>

    <svg class="emblem" viewBox="0 0 228 228">
      <path d="M 54 23 A 110 110 0 1 0 174 23" fill="none" stroke="var(--gold)" stroke-width="1.5"/>
      <circle cx="114" cy="114" r="104" fill="none" stroke="var(--gold)" stroke-width="1.5"/>
      <circle cx="114" cy="114" r="94" fill="none" stroke="var(--gold)" stroke-width="9"/>
      <circle cx="114" cy="114" r="86" fill="var(--label)"/>
      <ellipse cx="114" cy="112" rx="62" ry="72" fill="var(--art-green)" opacity="0.85"
        role="img" aria-label="Illustration of two cheerful cannabis bud characters standing side by side"/>
    </svg>

    <div class="volume">
      <p>16oz (0.473 liters)</p>
      <p>Net Weight - 1 lb (0.454 kg)</p>
    </div>
  </section>
</div>
</body>
</html>
```